Business card for Luxury Portable Restroom Trailer company

We are a Luxury Portable Restroom Trailer Company Called FALCRIDGE HIRES. Based in Orange County California. We provide portable restroom trailers for events, such as, Weddings, Concerts, Charity events, Sporting events, Tournaments, Corporate events, ect. We rent and Sell the Luxury restrooms. Our colors are white, grey, and Orange. As you will see in the logo we uploaded.
There are 2 people in the company so the names and titles will change for the 3 people but card will remain the same. Here is the information for each Person: Dwight Penner CFO 555 318-0476
next Person: Leon Marchetti VP 555 318-0476
Next Person: Owen Marchetti CEO 555 318-0476
Information to include on the card: Luxury Restroom Trailers Rental and Sales. Weddings, Concerts, Charity, Sporting and Corp. Events.

```html
<!DOCTYPE html>
<html lang="en">
<head>
<meta charset="utf-8">
<title>Falcridge Hires – Business Card</title>
<link rel="stylesheet" href="https://fonts.googleapis.com/css2?family=Montserrat:wght@400;600&display=swap">
<style>
  :root{
    --page:#e4dfd8;
    --card-dark:#3a3837;
    --card-mid:#4a4847;
    --orange:#e8641c;
    --orange-deep:#d4521a;
    --silver:#dcd8d3;
    --silver-light:#f1efec;
    --text-light:#e9e6e2;
    --text-muted:#c9bfb4;
  }
  *{margin:0;padding:0;box-sizing:border-box}
  html,body{width:1200px;height:897px;overflow:hidden;background:var(--page)}
  body{font-family:"Montserrat",sans-serif;position:relative}
  .card{
    position:absolute;left:60px;top:155px;width:1080px;height:587px;
    border-radius:22px;overflow:hidden;
    background:linear-gradient(135deg,var(--card-mid) 0%,var(--card-dark) 60%);
    box-shadow:0 14px 40px rgba(0,0,0,.22);
  }
  .accent-band{
    position:absolute;left:796px;top:0;right:0;bottom:0;
    background:linear-gradient(180deg,var(--orange) 0%,var(--orange-deep) 100%);
  }
  .emblem{position:absolute;left:562px;top:62px;width:460px;height:460px}
  .emblem-name{
    position:absolute;left:562px;top:62px;width:460px;height:460px;
    display:flex;align-items:center;justify-content:center;
    font-weight:600;font-size:34px;letter-spacing:2px;color:var(--orange);
  }
  .brand-name{
    position:absolute;left:61px;top:96px;
    font-weight:600;font-size:38px;letter-spacing:2px;color:var(--orange);
  }
  .name-marker{position:absolute;left:0;top:230px;width:30px;height:65px;background:var(--orange)}
  .person-name{
    position:absolute;left:61px;top:224px;
    font-weight:600;font-size:41px;letter-spacing:1.5px;color:var(--orange);
  }
  .person-title{
    position:absolute;left:61px;top:276px;
    font-weight:400;font-size:24px;letter-spacing:1px;color:var(--text-light);
  }
  .contact{position:absolute;left:56px;top:335px;list-style:none}
  .contact li{
    display:flex;align-items:center;gap:10px;height:37px;
    font-size:24px;color:var(--text-light);letter-spacing:.5px;
  }
  .contact svg{width:20px;height:20px;flex:none}
  .tagline{
    position:absolute;left:56px;top:466px;
    font-weight:600;font-size:22px;letter-spacing:.8px;color:var(--orange);
  }
  .services{
    position:absolute;left:56px;top:497px;
    font-weight:400;font-size:23.5px;letter-spacing:.8px;color:var(--text-muted);
  }
</style>
</head>
<body>
  <div class="card">
    <div class="accent-band"></div>

    <svg class="emblem" viewBox="0 0 460 460" aria-hidden="true">
      <defs>
        <radialGradient id="silverFill" cx="45%" cy="35%" r="70%">
          <stop offset="0" stop-color="#f4f2ef"/>
          <stop offset="1" stop-color="#cfcac4"/>
        </radialGradient>
      </defs>
      <circle cx="230" cy="230" r="228" fill="url(#silverFill)"/>
      <circle cx="230" cy="230" r="187" fill="none" stroke="#e8641c" stroke-width="16"/>
    </svg>
    <div class="emblem-name">FALCRIDGE HIRES</div>

    <div class="brand-name">FALCRIDGE HIRES</div>

    <div class="name-marker"></div>
    <h1 class="person-name">OWEN MARCHETTI</h1>
    <p class="person-title">CEO</p>

    <ul class="contact">
      <li>
        <svg viewBox="0 0 24 24"><path fill="#e8641c" d="M6.6 10.8a15.2 15.2 0 0 0 6.6 6.6l2.2-2.2c.3-.3.7-.4 1-.2 1.1.4 2.3.6 3.6.6.6 0 1 .4 1 1V20c0 .6-.4 1-1 1A17 17 0 0 1 3 4c0-.6.4-1 1-1h3.5c.6 0 1 .4 1 1 0 1.3.2 2.5.6 3.6.1.3 0 .7-.2 1z"/></svg>
        555 318-0476
      </li>
      <li>
        <svg viewBox="0 0 24 24"><rect x="2" y="5" width="20" height="14" rx="2" fill="#e8641c"/><path d="M3 6l9 7 9-7" fill="none" stroke="#3a3837" stroke-width="1.6"/></svg>
        owen@falcridgehires.com
      </li>
      <li>
        <svg viewBox="0 0 24 24"><circle cx="12" cy="12" r="10" fill="#e8641c"/><path d="M2 12h20M12 2c3 3 3 17 0 20M12 2c-3 3-3 17 0 20" fill="none" stroke="#3a3837" stroke-width="1.4"/></svg>
        www.falcridgehires.com
      </li>
    </ul>

    <p class="tagline">Luxury Restroom Trailers Rental and Sales</p>
    <p class="services">Weddings | Concerts | Charity | Sporting | Corp</p>
  </div>
</body>
</html>
```